Kelvor Engineers: Why you should hire us keepsake

New design. Open to plastic cards. We are an engineering firm that designs cell phone towers and commercial buildings. Please check out our website www.kelvorstruct.com for more details. We want people to remember our card and for it to be useful if possible. We want the same look and feel on these cards to be translated to other marketing material we may need such as brochures.

Target Market(s)

Architects, Developers and Telecommunication Carriers

Industry/Entity Type

Engineering

Contact Information for Business Card

Card with our company colors, logo, and innovative design with elements related to our industry.

Font styles to use
Sans Serif

Colors
9bcb3c
abd036
0255a3

Requirements
Must have
• Sleek and hip design
Nice to have
• Bright lime green and navy coloring that pops with an innovative design.
Should not have
• A basic and boring design

```html
<!DOCTYPE html>
<html lang="en">
<head>
<meta charset="utf-8">
<title>Kelvor Engineers – Business Card</title>
<link rel="stylesheet" href="https://fonts.googleapis.com/css2?family=Roboto:wght@400;500;700;900&family=Roboto+Condensed:wght@700&display=swap">
<style>
  :root {
    --bg: #d9d6d2;
    --navy: #0a2d5c;
    --lime: #1ef01e;
    --paper: #f3f3f3;
    --ink: #4a4a4a;
    --white: #ffffff;
  }
  * { margin: 0; padding: 0; box-sizing: border-box; }
  html, body { width: 1200px; height: 960px; overflow: hidden; }
  body {
    background: var(--bg);
    position: relative;
    font-family: "Roboto", Arial, sans-serif;
  }
  .card {
    position: absolute;
    width: 600px;
    height: 342px;
    border-radius: 18px;
  }
  .card--front {
    left: 320px; top: 108px;
    background: var(--navy);
    color: var(--white);
    text-align: center;
  }
  .front-name {
    position: absolute;
    left: 0; right: 0; top: 120px;
    font-weight: 900;
    font-size: 58px;
    letter-spacing: -1px;
    color: var(--lime);
  }
  .tagline {
    position: absolute;
    left: 0; right: 0; top: 265px;
    font-weight: 500;
    font-size: 15px;
    letter-spacing: 0.2px;
    display: flex; align-items: center; justify-content: center; gap: 4px;
  }
  .tagline::before, .tagline::after {
    content: ""; width: 28px; height: 1.5px; background: var(--white);
  }
  .locations {
    position: absolute;
    left: 0; right: 0; top: 286px;
    font-size: 15px;
    letter-spacing: 0.6px;
  }
  .card--back {
    left: 320px; top: 493px;
    background: var(--paper);
  }
  .back-name {
    position: absolute;
    right: 40px; top: 40px;
    font-weight: 900;
    font-size: 34px;
    letter-spacing: -0.5px;
    color: var(--lime);
  }
  .tab {
    position: absolute;
    left: 0; top: 200px;
    width: 12px; height: 25px;
    background: var(--navy);
    border-radius: 0 5px 5px 0;
  }
  .person {
    position: absolute;
    left: 35px; top: 202px;
    font-family: "Roboto Condensed", Arial, sans-serif;
    font-weight: 700;
    font-size: 21px;
    color: var(--lime);
  }
  .contacts {
    position: absolute;
    left: 35px; top: 236px;
    list-style: none;
  }
  .contacts li {
    display: flex; align-items: center;
    height: 19.5px;
    font-size: 14px;
    color: var(--ink);
  }
  .contacts svg { width: 13px; height: 13px; margin-right: 10px; fill: var(--lime); }
</style>
</head>
<body>
  <section class="card card--front">
    <div class="front-name">Kelvor Engineers</div>
    <div class="tagline">MULTI-DISCIPLINE ENGINEERING</div>
    <div class="locations">Denver | Raleigh | Phoenix | San Diego</div>
  </section>

  <section class="card card--back">
    <div class="back-name">Kelvor Engineers</div>
    <span class="tab"></span>
    <h1 class="person">DANA WHITCOMBE FERRIS</h1>
    <ul class="contacts">
      <li><svg viewBox="0 0 16 16"><path d="M3.6 1l2.6 3-1.4 1.8c.9 2 2.5 3.6 4.5 4.5l1.8-1.4 3 2.6-1.4 2.5C7.4 14.3 1.7 8.6 1.1 2.4z"/></svg>555.314.0147</li>
      <li><svg viewBox="0 0 16 16"><path d="M4 0h8a1 1 0 0 1 1 1v14a1 1 0 0 1-1 1H4a1 1 0 0 1-1-1V1a1 1 0 0 1 1-1zm1 2v10h6V2zm2 11v1.5h2V13z"/></svg>555.762.0193</li>
      <li><svg viewBox="0 0 16 16"><path d="M1 3h14v1.2L8 9 1 4.2zm0 2.6l7 4.8 7-4.8V13H1z"/></svg>dferris@kelvorstruct.com</li>
      <li><svg viewBox="0 0 16 16"><circle cx="8" cy="8" r="7"/></svg>www.kelvorstruct.com</li>
    </ul>
  </section>
</body>
</html>
```